Home Baker of cakes, muffins, cookies and pastries.

I am looking for business cards for my home baking business called " Yum Bea-A Treat " - I want them to be super cute and girly, yet simple and modern at the same time. Pastel colours is what I envision with the main colour being baby pink.

```html
<!DOCTYPE html>
<html lang="en">
<head>
<meta charset="utf-8">
<title>Yum Bea-A Treat — Business Cards</title>
<link rel="stylesheet" href="https://fonts.googleapis.com/css2?family=Roboto:wght@400;500;700&display=swap">
<style>
  :root {
    --page-bg: #ececec;
    --card-white: #f5f4f4;
    --baby-pink: #e9408e;
    --soft-pink: #f4a6c6;
    --pale-pink: #f9d3e3;
    --text-pink: #d43d85;
    --white: #ffffff;
  }
  * { box-sizing: border-box; margin: 0; padding: 0; }
  html, body { width: 675px; height: 1200px; overflow: hidden; }
  body {
    background: var(--page-bg);
    font-family: "Roboto", Arial, sans-serif;
    position: relative;
  }
  .card {
    position: absolute;
    overflow: hidden;
  }
  .card--front {
    top: 512px; left: 37px;
    width: 286px; height: 171px;
    background: var(--card-white);
    border-radius: 26px 12px 12px 24px;
  }
  .card--back {
    top: 509px; left: 334px;
    width: 291px; height: 174px;
    background: var(--baby-pink);
    border-radius: 10px;
  }

  .art-placeholder {
    position: absolute;
    border-radius: 40% 40% 8px 8px;
  }
  .card--front .art-placeholder {
    left: 222px; top: 28px; width: 80px; height: 143px;
    background: linear-gradient(180deg, rgba(249, 211, 227, 0.75), rgba(244, 166, 198, 0.45));
  }
  .art-placeholder--edge {
    left: -14px; top: 16px; width: 92px; height: 158px;
    background: linear-gradient(180deg, rgba(255, 255, 255, 0.35), rgba(249, 211, 227, 0.55));
  }
  .art-placeholder--centre {
    left: 140px; top: 39px; width: 70px; height: 70px;
    background: linear-gradient(180deg, rgba(255, 255, 255, 0.95), rgba(249, 211, 227, 0.9));
  }

  .wordmark {
    position: absolute;
    font-weight: 700;
    white-space: nowrap;
    display: flex;
    align-items: center;
    gap: 5px;
  }
  .wordmark__dot { width: 8px; height: 8px; border-radius: 50%; flex: none; }
  .card--front .wordmark {
    top: 52px; left: 28px;
    font-size: 19px; color: var(--text-pink);
  }
  .card--front .wordmark__dot { background: var(--text-pink); }
  .card--back .wordmark {
    top: 114px; left: 122px;
    font-size: 16px; color: var(--white);
  }
  .card--back .wordmark__dot { background: var(--white); }

  .contact-name {
    position: absolute; top: 110px; left: 13px;
    font-size: 11px; color: var(--text-pink); line-height: 1.15;
  }
  .contact-role { color: var(--soft-pink); display: block; }
  .contact-list {
    position: absolute; top: 140px; left: 12px;
    list-style: none; font-size: 8px; color: var(--text-pink);
  }
  .contact-list li { display: flex; align-items: center; gap: 4px; margin-bottom: 3px; }
  .contact-icon { width: 11px; height: 11px; flex: none; }
  .contact-web {
    position: absolute; top: 156px; right: 22px;
    font-size: 7.5px; font-weight: 700; color: var(--text-pink); letter-spacing: 0.2px;
  }
</style>
</head>
<body>
  <section class="card card--front" aria-label="Business card front">
    <div class="art-placeholder" role="img" aria-label="Faint pastel pink cupcake illustration"></div>
    <div class="wordmark"><span class="wordmark__dot"></span>Yum Bea-A Treat</div>
    <p class="contact-name">Bea Lawson<span class="contact-role">Chef</span></p>
    <ul class="contact-list">
      <li>
        <svg class="contact-icon" viewBox="0 0 12 12" aria-hidden="true">
          <circle cx="6" cy="6" r="5.3" fill="none" stroke="#d43d85" stroke-width="1.2"/>
          <rect x="3.6" y="3.3" width="4.8" height="5.4" rx="1" fill="#d43d85"/>
        </svg>
        0400 318 257
      </li>
      <li>
        <svg class="contact-icon" viewBox="0 0 12 12" aria-hidden="true">
          <circle cx="6" cy="6" r="5.3" fill="none" stroke="#d43d85" stroke-width="1.2"/>
          <rect x="3.3" y="4" width="5.4" height="4" fill="none" stroke="#d43d85" stroke-width="0.9"/>
          <polyline points="3.3,4 6,6.2 8.7,4" fill="none" stroke="#d43d85" stroke-width="0.9"/>
        </svg>
        hello@yumbeatreat.com.au
      </li>
    </ul>
    <p class="contact-web">www.yumbea-a-treat.com</p>
  </section>

  <section class="card card--back" aria-label="Business card back">
    <div class="art-placeholder art-placeholder--edge" role="img" aria-label="Large faint cupcake illustration continuing from the front"></div>
    <div class="art-placeholder art-placeholder--centre" role="img" aria-label="White cupcake illustration above the name"></div>
    <div class="wordmark"><span class="wordmark__dot"></span>Yum Bea-A Treat</div>
  </section>
</body>
</html>
```